Business card - Harbor Crest Builders

Design a business card utilizing the given logo.
colors we like: Black, greys, Teal, blues.
Tri color card, horizontal orientation likely
Logo and name likely best on top.
Info on card:

Dennis Farrow
#8 - 4815 Alder Ridge Blvd.
Surrey, B.C. V3K 2R9

778.555.0193
dennisfarrow@tellmail.ca

Slogan: "Building Dreams"

We are a construction company that specializes in new home construction on the West coast of BC Canada. Open Concepts designs of high end homes.

```html
<!DOCTYPE html>
<html lang="en">
<head>
<meta charset="utf-8">
<title>Harbor Crest Builders – Business Card</title>
<link rel="stylesheet" href="https://fonts.googleapis.com/css2?family=Exo+2:wght@500;600&family=Nunito+Sans:wght@400;600&display=swap">
<style>
  :root {
    --backdrop: #7a7a7a;
    --card-white: #ffffff;
    --card-black: #000000;
    --ink-black: #111111;
    --ink-white: #ffffff;
    --ink-soft: #e6e6e6;
    --accent-grey: #3a3a3a;
  }
  html, body {
    margin: 0;
    padding: 0;
    width: 1200px;
    height: 1000px;
    overflow: hidden;
    background: var(--backdrop);
  }
  .business-card {
    position: absolute;
    left: 150px;
    top: 222px;
    width: 900px;
    height: 556px;
    overflow: hidden;
    background: var(--card-black);
    box-shadow: 0 6px 18px rgba(0,0,0,0.35);
  }
  .brand-band {
    position: absolute;
    left: 0;
    top: 0;
    width: 900px;
    height: 203px;
    background: var(--card-white);
    display: flex;
    align-items: center;
    justify-content: center;
    gap: 26px;
  }
  .brand-dot {
    width: 96px;
    height: 96px;
    border-radius: 50%;
    background: var(--ink-black);
    flex: none;
  }
  .brand-name {
    font-family: "Exo 2", sans-serif;
    font-weight: 600;
    font-size: 52px;
    letter-spacing: 1px;
    text-transform: uppercase;
    color: var(--ink-black);
    line-height: 1;
  }
  .accent-circle {
    position: absolute;
    left: 624px;
    top: 235px;
    width: 324px;
    height: 324px;
    border-radius: 50%;
    background: var(--accent-grey);
  }
  .holder {
    position: absolute;
    left: 478px;
    top: 236px;
  }
  .holder-name {
    margin: 0;
    font-family: "Exo 2", sans-serif;
    font-weight: 600;
    font-size: 37px;
    letter-spacing: 1.5px;
    color: var(--ink-white);
    line-height: 1.1;
  }
  .holder-title {
    margin: 4px 0 0;
    font-family: "Nunito Sans", sans-serif;
    font-size: 22px;
    color: var(--ink-soft);
  }
  .contact-list {
    position: absolute;
    left: 80px;
    top: 398px;
    margin: 0;
    padding: 0;
    list-style: none;
    font-family: "Nunito Sans", sans-serif;
    font-size: 23px;
    color: var(--ink-white);
  }
  .contact-item {
    display: flex;
    align-items: center;
    gap: 12px;
    height: 34px;
  }
  .contact-icon {
    width: 21px;
    height: 21px;
    flex: none;
  }
</style>
</head>
<body>
  <article class="business-card">
    <header class="brand-band">
      <span class="brand-dot"></span>
      <span class="brand-name">Harbor Crest Builders</span>
    </header>

    <div class="accent-circle"></div>

    <section class="holder">
      <h1 class="holder-name">Dennis Farrow</h1>
      <p class="holder-title">Managing Director</p>
    </section>

    <ul class="contact-list">
      <li class="contact-item">
        <svg class="contact-icon" viewBox="0 0 20 20" aria-hidden="true">
          <rect width="20" height="20" rx="3" fill="#fff"/>
          <path d="M6 4.5l2.2 0 1 3-1.4 1.1c.7 1.5 1.8 2.6 3.3 3.3l1.1-1.4 3 1v2.2c0 .7-.6 1.3-1.3 1.3C8.9 15 5 11.1 5 5.8c0-.7.4-1.3 1-1.3z" fill="#000"/>
        </svg>
        <span>778.555.0193</span>
      </li>
      <li class="contact-item">
        <svg class="contact-icon" viewBox="0 0 20 20" aria-hidden="true">
          <rect width="20" height="20" rx="3" fill="#fff"/>
          <rect x="4" y="6" width="12" height="8.5" rx="1" fill="#000"/>
          <path d="M4.5 6.6L10 10.6l5.5-4" stroke="#fff" stroke-width="1.2" fill="none"/>
        </svg>
        <span>dennisfarrow@tellmail.ca</span>
      </li>
      <li class="contact-item">
        <svg class="contact-icon" viewBox="0 0 20 20" aria-hidden="true">
          <rect width="20" height="20" rx="3" fill="#fff"/>
          <path d="M10 3.5c-2.6 0-4.5 1.9-4.5 4.4 0 3.2 4.5 8.6 4.5 8.6s4.5-5.4 4.5-8.6c0-2.5-1.9-4.4-4.5-4.4z" fill="#000"/>
          <circle cx="10" cy="8" r="1.7" fill="#fff"/>
        </svg>
        <span>#8 - 4815 Alder Ridge Blvd. Surrey, B.C. V3K 2R9</span>
      </li>
    </ul>
  </article>
</body>
</html>
```